Full re-design of visual identity

We have just re-designed our logo and would like to apply it on our folders, business cards, stationery, and etc... we are attaching new logo + the material we need to re-design... we will provide full corel draw files to help make job easier and also because lot of icons and artwork can be still used...

any doubts we are at your disposal. thanks in advance.

```html
<!DOCTYPE html>
<html lang="en">
<head>
<meta charset="utf-8">
<title>Corvalink Letterhead</title>
<link href="https://fonts.googleapis.com/css2?family=Exo+2:ital,wght@0,300;0,400;0,600;0,700;1,400;1,600&family=Dancing+Script:wght@500&display=swap" rel="stylesheet">
<style>
  :root{
    --bg:#f4f4f4;
    --paper:#ffffff;
    --brand-orange:#ee7a33;
    --brand-grey:#7b7b7b;
    --ink:#6a6a6a;
    --ink-dark:#333333;
    --rule:#8a8a8a;
  }
  *{margin:0;padding:0;box-sizing:border-box}
  html,body{width:1200px;height:1000px;overflow:hidden;background:var(--bg)}
  body{position:relative;font-family:"Exo 2",sans-serif;color:var(--ink)}
  .sheet{position:absolute;top:193px;width:439px;height:612px;background:var(--paper)}
  .sheet--classic{left:132px}
  .sheet--stacked{left:614px}
  .brand{position:absolute;right:44px;top:36px;display:flex;align-items:center;gap:6px}
  .brand__name{font-weight:700;font-size:34px;letter-spacing:-1px;color:var(--brand-grey);line-height:1}
  .brand__dot{width:18px;height:18px;border-radius:50%;background:var(--brand-orange)}
  .meta{position:absolute;left:60px;display:flex}
  .meta--row{top:156px;gap:26px}
  .meta--column{top:112px;flex-direction:column;gap:5px}
  .meta__label{font-weight:700;font-size:8px;color:var(--brand-orange);line-height:1.1}
  .meta__value{font-style:italic;font-size:6.5px;color:var(--ink);line-height:1.1}
  .rule{position:absolute;left:60px;right:44px;height:1px;background:var(--rule)}
  .rule--top{top:176px}
  .rule--bottom{top:486px}
  .letter__heading{position:absolute;right:44px;top:197px;font-style:italic;font-weight:600;font-size:11px;color:var(--brand-orange)}
  .letter__body{position:absolute;left:100px;right:44px;font-size:6.2px;line-height:11.4px;text-align:justify;font-weight:400;color:var(--ink)}
  .letter__body--first{top:221px}
  .letter__body--second{top:319px}
  .letter__closing{position:absolute;left:100px;top:420px;font-size:6.2px}
  .letter__signature{position:absolute;right:44px;top:444px;font-family:"Dancing Script",cursive;font-size:22px;color:var(--ink-dark)}
  .contact{position:absolute;left:310px;top:511px;list-style:none;font-size:6px;color:var(--ink);line-height:8px}
  .contact__item{display:flex;gap:4px;align-items:flex-start;margin-bottom:3px}
  .contact__item--divided{padding-bottom:2px;position:relative}
  .contact__item--divided::after{content:"";position:absolute;left:10px;bottom:-1px;width:31px;height:1px;background:var(--rule)}
  .contact__icon{width:6px;height:6px;flex:none;margin-top:1px}
  .sheet__band{position:absolute;left:0;right:0;bottom:0;height:9px;background:var(--brand-orange)}
</style>
</head>
<body>

<!-- Letterhead, version with meta row -->
<section class="sheet sheet--classic">
  <div class="brand"><span class="brand__name">corvalink</span><span class="brand__dot"></span></div>
  <div class="meta meta--row">
    <div><p class="meta__label">SUBJECT</p><p class="meta__value">lorem ipsum</p></div>
    <div><p class="meta__label">DATE</p><p class="meta__value">01/01/2014</p></div>
    <div><p class="meta__label">ADRESSED TO</p><p class="meta__value">Mara Lind</p></div>
  </div>
  <div class="rule rule--top"></div>
  <h1 class="letter__heading">Lorem ipsum dolor sit ametconsectetur.</h1>
  <p class="letter__body letter__body--first">Lorem ipsum dolor sit amet, consectetur adipiscing elit. Nulla sodales nisi vitae Lorem ipsum dolor sit amet, consectetur adipiscing elit. Suspendisse feugiat eros nisl, a facilisis risus eleifend sed. Aliquam mauris enim, fermentum eu lacinia sit amet, laoreet eu leo. Nullam eleifend nulla in libero tristique, ac vulputate odio tincidunt. Etiam non condimentum tortor. Integer suscipit neque nec odio porttitor cursus. Phasellus a sapien blandit, suscipit justo id, condimentum ante. Morbi tristique justo risus, id mattis dui molestie ut. Nullam volutpat ut quam commodo faucibus. Pellentesque urna est, interdum in elit quis, pharetra elementum orci. Nam placerat velit molestie justo placerat scelerisque.</p>
  <p class="letter__body letter__body--second">Ut vitae interdum diam, in euismod ante. Pellentesque volutpat, risus sit amet sodales hendrerit, mi turpis vulputate dolor, eget cursus nulla eros nec tellus. Nulla tincidunt molestie libero vel pretium. Donec condimentum nulla sit amet risus semper imperdiet. Duis congue eros nec diam blandit, et pellentesque sapien auctor. Curabitur iaculis enim lectus, in imperdiet mauris mattis eget. Etiam ac ornare metus. Mauris risus leo, egestas at dolor a, ultrices adipiscing est. Nunc faucibus scelerisque mollis. Pellentesque aliquet mauris tellus, id dignissim risus viverra et. Mauris venenatis lobortis eros. Nam id diam in ligula malesuada feugiat. Cras turpis felis, aliquet id mauris elementum, feugiat ultricies nisl.</p>
  <p class="letter__closing">Best regards.</p>
  <p class="letter__signature">Paul Hartley</p>
  <div class="rule rule--bottom"></div>
  <ul class="contact">
    <li class="contact__item contact__item--divided"><svg class="contact__icon" viewBox="0 0 10 10"><path d="M5 0a3.5 3.5 0 0 0-3.5 3.5C1.5 6 5 10 5 10s3.5-4 3.5-6.5A3.5 3.5 0 0 0 5 0z" fill="var(--brand-orange)"/></svg><span>48, Harbor Lane, Westfield,<br>20410, Norland</span></li>
    <li class="contact__item"><svg class="contact__icon" viewBox="0 0 10 10"><path d="M2 0l2 2.5-1 1.2a6 6 0 0 0 3.3 3.3l1.2-1L10 8l-1.5 2C4 10 0 6 0 1.5z" fill="var(--brand-orange)"/></svg><span>555-2087-41</span></li>
    <li class="contact__item contact__item--divided"><svg class="contact__icon" viewBox="0 0 10 10"><rect x="0" y="2" width="10" height="7" rx="1" fill="var(--brand-orange)"/></svg><span>555-2087-42</span></li>
    <li class="contact__item"><svg class="contact__icon" viewBox="0 0 10 10"><rect x="0" y="2" width="10" height="6.5" fill="var(--brand-orange)"/><path d="M0 2l5 4 5-4" stroke="#fff" fill="none"/></svg><span>hello@corvalink.com</span></li>
    <li class="contact__item"><svg class="contact__icon" viewBox="0 0 10 10"><circle cx="5" cy="5" r="5" fill="var(--brand-orange)"/><path d="M0 5h10M5 0c-2.5 3-2.5 7 0 10M5 0c2.5 3 2.5 7 0 10" stroke="#fff" stroke-width=".8" fill="none"/></svg><span>www.corvalink.com</span></li>
  </ul>
  <div class="sheet__band"></div>
</section>

<!-- Letterhead, version with stacked meta -->
<section class="sheet sheet--stacked">
  <div class="brand"><span class="brand__name">corvalink</span><span class="brand__dot"></span></div>
  <div class="meta meta--column">
    <div><p class="meta__label">SUBJECT</p><p class="meta__value">lorem ipsum</p></div>
    <div><p class="meta__label">DATE</p><p class="meta__value">01/01/2014</p></div>
    <div><p class="meta__label">ADRESSED TO</p><p class="meta__value">Mara Lind</p></div>
  </div>
  <div class="rule rule--top"></div>
  <h1 class="letter__heading">Lorem ipsum dolor sit ametconsectetur.</h1>
  <p class="letter__body letter__body--first">Lorem ipsum dolor sit amet, consectetur adipiscing elit. Nulla sodales nisi vitae Lorem ipsum dolor sit amet, consectetur adipiscing elit. Suspendisse feugiat eros nisl, a facilisis risus eleifend sed. Aliquam mauris enim, fermentum eu lacinia sit amet, laoreet eu leo. Nullam eleifend nulla in libero tristique, ac vulputate odio tincidunt. Etiam non condimentum tortor. Integer suscipit neque nec odio porttitor cursus. Phasellus a sapien blandit, suscipit justo id, condimentum ante. Morbi tristique justo risus, id mattis dui molestie ut. Nullam volutpat ut quam commodo faucibus. Pellentesque urna est, interdum in elit quis, pharetra elementum orci. Nam placerat velit molestie justo placerat scelerisque.</p>
  <p class="letter__body letter__body--second">Ut vitae interdum diam, in euismod ante. Pellentesque volutpat, risus sit amet sodales hendrerit, mi turpis vulputate dolor, eget cursus nulla eros nec tellus. Nulla tincidunt molestie libero vel pretium. Donec condimentum nulla sit amet risus semper imperdiet. Duis congue eros nec diam blandit, et pellentesque sapien auctor. Curabitur iaculis enim lectus, in imperdiet mauris mattis eget. Etiam ac ornare metus. Mauris risus leo, egestas at dolor a, ultrices adipiscing est. Nunc faucibus scelerisque mollis. Pellentesque aliquet mauris tellus, id dignissim risus viverra et. Mauris venenatis lobortis eros. Nam id diam in ligula malesuada feugiat. Cras turpis felis, aliquet id mauris elementum, feugiat ultricies nisl.</p>
  <p class="letter__closing">Best regards.</p>
  <p class="letter__signature">Paul Hartley</p>
  <div class="rule rule--bottom"></div>
  <ul class="contact">
    <li class="contact__item contact__item--divided"><svg class="contact__icon" viewBox="0 0 10 10"><path d="M5 0a3.5 3.5 0 0 0-3.5 3.5C1.5 6 5 10 5 10s3.5-4 3.5-6.5A3.5 3.5 0 0 0 5 0z" fill="var(--brand-orange)"/></svg><span>48, Harbor Lane, Westfield,<br>20410, Norland</span></li>
    <li class="contact__item"><svg class="contact__icon" viewBox="0 0 10 10"><path d="M2 0l2 2.5-1 1.2a6 6 0 0 0 3.3 3.3l1.2-1L10 8l-1.5 2C4 10 0 6 0 1.5z" fill="var(--brand-orange)"/></svg><span>555-2087-41</span></li>
    <li class="contact__item contact__item--divided"><svg class="contact__icon" viewBox="0 0 10 10"><rect x="0" y="2" width="10" height="7" rx="1" fill="var(--brand-orange)"/></svg><span>555-2087-42</span></li>
    <li class="contact__item"><svg class="contact__icon" viewBox="0 0 10 10"><rect x="0" y="2" width="10" height="6.5" fill="var(--brand-orange)"/><path d="M0 2l5 4 5-4" stroke="#fff" fill="none"/></svg><span>hello@corvalink.com</span></li>
    <li class="contact__item"><svg class="contact__icon" viewBox="0 0 10 10"><circle cx="5" cy="5" r="5" fill="var(--brand-orange)"/><path d="M0 5h10M5 0c-2.5 3-2.5 7 0 10M5 0c2.5 3 2.5 7 0 10" stroke="#fff" stroke-width=".8" fill="none"/></svg><span>www.corvalink.com</span></li>
  </ul>
  <div class="sheet__band"></div>
</section>

</body>
</html>
```